TL - business card

Tallow Partners is an insurance brokerage firm, inovative, proactive, vigorous, which aims to become the leader of the insurance brokers in Anfrica. We should like to get some designs which should be avoided also in Gray / Metallic for the Administration and Orange / Blue for the Managers (ike in the picture sent). The Blue / Green logo is not the correct one, but the source of the file. Please adjust the color accordingly for the business cards. 1 / Orange / Blue 2 / Gray / Metallic We want something classic but which is transmitted strenght, inovation, modernity and most of all, rapidity. We want something start-up like, very punchy and catching eye remaining profesional at the same time. Name: Dorian Whitlock Function: Managing Director Address: N ° 17/18 Rua Veloso - R / C 2B Direita - Bairro Mutamba - Luanda Tel: (+244) 947 582 316 Email: dorian.whitlock@tallow-p.example Website: www.tallow-p. example We want classic in the front and creative, colorfull at the back. The cards will be printed in relief, with very high quality of paper.
Insurance Broker
Colors
Designer to choose colors to be used in the design.

```html
<!DOCTYPE html>
<html lang="en">
<head>
<meta charset="utf-8">
<title>Tallow Partners – Business Card</title>
<link rel="stylesheet" href="https://fonts.googleapis.com/css2?family=Maven+Pro:wght@500;700&family=Roboto:wght@400&display=swap">
<style>
  :root {
    --backdrop: #e4e6e8;
    --card: #f4f5f6;
    --card-edge: #d3d6d9;
    --accent-red: #d6372c;
    --accent-blue: #2f86c0;
    --text-dark: #3a3d40;
    --mark-tint: #e9ecef;
  }
  * { margin: 0; padding: 0; box-sizing: border-box; }
  html, body {
    width: 1200px; height: 969px; overflow: hidden;
    background: var(--backdrop);
  }
  .business-card {
    position: absolute; left: 100px; top: 200px;
    width: 1000px; height: 570px;
    background: var(--card);
    border: 1px solid var(--card-edge);
    border-radius: 24px;
    overflow: hidden;
    box-shadow: 0 18px 40px rgba(0,0,0,0.12);
  }
  .edge-band {
    position: absolute; right: 0; top: 0; bottom: 0; width: 62px;
    background: var(--accent-red);
  }
  .identity { position: absolute; left: 54px; top: 68px; }
  .person-name {
    font-family: "Maven Pro", sans-serif; font-weight: 700;
    font-size: 32px; color: var(--accent-red); letter-spacing: 0.5px;
  }
  .person-role {
    font-family: "Maven Pro", sans-serif; font-weight: 500;
    font-size: 23px; color: var(--accent-blue); margin-top: 2px;
  }
  .address {
    position: absolute; left: 54px; top: 230px;
    font-family: "Roboto", sans-serif; font-size: 22px; line-height: 30px;
    color: var(--text-dark); font-style: normal;
  }
  .contact-list {
    position: absolute; left: 54px; top: 340px; list-style: none;
    font-family: "Roboto", sans-serif; font-size: 22px; line-height: 30px;
    color: var(--text-dark);
  }
  .contact-list li { display: flex; align-items: center; gap: 12px; }
  .contact-list svg { width: 19px; height: 19px; fill: var(--accent-red); flex: none; }
  .company-name {
    position: absolute; left: 54px; top: 470px;
    font-family: "Maven Pro", sans-serif; font-weight: 700;
    font-size: 35px; color: var(--accent-red); letter-spacing: 1px;
  }
  .brand-spot {
    position: absolute; left: 500px; top: 70px; width: 420px; height: 420px;
  }
  .brand-spot .disc {
    position: absolute; inset: 0; border-radius: 50%;
    background: var(--mark-tint);
  }
  .brand-spot .brand-name {
    position: absolute; inset: 0; display: flex; align-items: center; justify-content: center;
    font-family: "Maven Pro", sans-serif; font-weight: 700;
    font-size: 40px; color: var(--accent-blue); letter-spacing: 1px;
  }
</style>
</head>
<body>
  <main class="business-card">
    <div class="edge-band"></div>

    <header class="identity">
      <h1 class="person-name">Dorian Whitlock</h1>
      <p class="person-role">Managing Director</p>
    </header>

    <address class="address">
      N ° 17/18 Rua Veloso<br>
      R / C 2B Direita<br>
      Bairro Mutamba, Luanda
    </address>

    <ul class="contact-list">
      <li>
        <svg viewBox="0 0 24 24" aria-hidden="true"><path d="M6.6 10.8a15.1 15.1 0 0 0 6.6 6.6l2.2-2.2a1 1 0 0 1 1-.25 11.4 11.4 0 0 0 3.6.57 1 1 0 0 1 1 1V20a1 1 0 0 1-1 1A17 17 0 0 1 3 4a1 1 0 0 1 1-1h3.5a1 1 0 0 1 1 1c0 1.25.2 2.45.57 3.57a1 1 0 0 1-.25 1z"/></svg>
        (+244) 947 582 316
      </li>
      <li>
        <svg viewBox="0 0 24 24" aria-hidden="true"><path d="M2 5h20v14H2z M2 5l10 7 10-7" fill="var(--accent-red)"/><path d="M3 6l9 6.3L21 6" fill="none" stroke="#f4f5f6" stroke-width="1.6"/></svg>
        dorian.whitlock@tallow-p.example
      </li>
      <li>
        <svg viewBox="0 0 24 24" aria-hidden="true"><circle cx="12" cy="12" r="10"/><path d="M2 12h20M12 2c3 3 3 17 0 20M12 2c-3 3-3 17 0 20" fill="none" stroke="#f4f5f6" stroke-width="1.4"/></svg>
        www.tallow-p. example
      </li>
    </ul>

    <p class="company-name">TALLOW PARTNERS</p>

    <div class="brand-spot">
      <div class="disc"></div>
      <p class="brand-name">TALLOW PARTNERS</p>
    </div>
  </main>
</body>
</html>
```